High-End Print/Digital Ad for Unique Luxury Travel Company Required

Objective:
Design a compelling and visually striking advertisement that highlights our company’s unmatched luxury travel experiences. The ad should elevate our brand image, spark curiosity, and drive prospective clients to contact us.
Target Audience:
• Affluent individuals seeking extraordinary, tailor-made travel experiences
• Affluent, luxury, high-net-worth individuals looking for value, expertise, and white-glove service
• Professionals or retirees who appreciate unique, thoughtfully curated travel over mainstream tourism
Key Messages to Communicate:
• One-of-a-kind luxury travel: Once-in-a-lifetime experiences that are curated with creativity and meticulous attention to detail
• Exceptional service: White-glove, personalized planning from start to finish
• 38 years’ travel experience – expert knowledge of destinations, modes of travel, premium accommodations and well-established, meaningful industry connections.
• Highly trusted: Cruise line executives often say, “No one does what you do.”
Tone and Style:
• Elegant, luxurious, sophisticated
• Eye-catching, polished, and modern
• Professional but warm—conveys trust and credibility
• High-impact visuals (full-bleed imagery, custom graphics, or high-end photography)
Deliverables:
• One full-page print ad and digital ad
• Ready-to-print, high-resolution file + working file (PSD, AI, etc.)
Optional: Social media-optimized version or short motion-graphic variation (if designer offers it)
Inspiration & Visual Style Suggestions:
• Think Lumen Voyages, Harrow Pike Wanderer, Silver Quill, or Orvel Retreats ad styles
• Large, emotive imagery with elegant typography
• Clean layout that speaks luxury, clarity, and trust
Copy Direction (draft):
For those who’ve explored the world—and crave something beyond the ordinary.
Each journey is a masterfully curated experience, rich in detail, seamless in execution, and unforgettable in every way.
Founded in 1997, Tidewell Journeys is a unique travel company specializing in cruising, all-inclusive luxury properties, and tours world-wide for individuals, groups, and incentives.
We offer an exceptional range of services designed to ensure every journey is flawlessly executed and truly unforgettable.
Let us help you plan your next extraordinary adventure.
Note: You may refine the copy slightly based on layout or format needs.
Other Resources for References:
1. Website - www.tidewelljourneys-example.com

```html
<!DOCTYPE html>
<html lang="en">
<head>
<meta charset="utf-8">
<title>Tidewell Journeys – Ad Campaign</title>
<link rel="stylesheet" href="https://fonts.googleapis.com/css2?family=Tinos:wght@400;700&family=Montserrat:wght@300;400&display=swap">
<style>
  :root {
    --board: #dedede;
    --paper: #ffffff;
    --ink: #0d0d0d;
    --label: #4a4a4a;
    --rule: #4a4a4a;
    --sky-gold: #f4b64e;
    --sky-amber: #ec8f3c;
    --sun-core: #fffbd8;
    --sun-glow: #ffe27a;
    --hull-warm: #a4583c;
    --sea-mid: #5a2f22;
    --sea-deep: #22130e;
    --glint: #ff9a2e;
    --on-photo: #ffffff;
  }
  * { margin: 0; padding: 0; box-sizing: border-box; }
  html, body { width: 1200px; height: 800px; overflow: hidden; background: var(--board); }
  .board { position: relative; width: 1200px; height: 800px; background: var(--board); }

  .callouts { position: absolute; inset: 0; }
  .format-label {
    position: absolute; right: 69px;
    font-family: "Montserrat", sans-serif; font-weight: 300;
    font-size: 15px; letter-spacing: 0.04em; color: var(--label);
    line-height: 1;
  }
  .label-print { top: 50px; }
  .label-social { top: 84px; }
  .label-banner { top: 117px; }

  .ad { position: absolute; background: var(--paper); overflow: hidden; }
  .ad .photo { position: absolute; inset: 0; width: 100%; height: 100%; }

  .headline {
    position: absolute; font-family: "Tinos", serif; font-weight: 700;
    color: var(--ink); text-transform: uppercase; letter-spacing: 0.01em;
  }
  .headline .lead, .headline .kicker { display: block; }
  .headline .kicker { letter-spacing: 0.03em; }

  .brand-name {
    position: absolute; font-family: "Tinos", serif; font-weight: 400;
    color: var(--on-photo); text-transform: uppercase; letter-spacing: 0.05em;
    white-space: nowrap; line-height: 1;
  }

  /* Print ad */
  .ad-print { left: 41px; top: 40px; width: 500px; height: 703px; }
  .ad-print .headline { left: 27px; top: 17px; }
  .ad-print .lead { font-size: 38px; line-height: 37.5px; }
  .ad-print .kicker { font-size: 17.3px; line-height: 20px; margin-top: 2px; }
  .ad-print .body-copy {
    position: absolute; left: 27px; top: 533px;
    font-family: "Montserrat", sans-serif; font-weight: 400;
    font-size: 10.2px; line-height: 13px; color: var(--on-photo);
  }
  .ad-print .body-copy p + p { margin-top: 14.5px; }
  .ad-print .brand-name { left: 27px; top: 657px; font-size: 15px; }

  /* Digital banner */
  .ad-banner { left: 765px; top: 199px; width: 365px; height: 138px; }
  .ad-banner .headline { left: 14px; top: 10px; }
  .ad-banner .lead { font-size: 18.5px; line-height: 18.8px; }
  .ad-banner .kicker { font-size: 9px; line-height: 10.4px; }
  .ad-banner .brand-name { right: 10px; top: 119px; font-size: 8.5px; }

  /* Social media ad */
  .ad-social { left: 765px; top: 378px; width: 365px; height: 365px; }
  .ad-social .headline { left: 17px; top: 12px; }
  .ad-social .lead { font-size: 28px; line-height: 27.8px; }
  .ad-social .kicker { font-size: 12.6px; line-height: 15px; margin-top: 1px; }
  .ad-social .brand-name { left: 17px; top: 337px; font-size: 12px; }
</style>
</head>
<body>
<div class="board">

  <svg class="callouts" width="1200" height="800" viewBox="0 0 1200 800" aria-hidden="true">
    <defs>
      <linearGradient id="sceneTones" x1="0" y1="0" x2="0" y2="1">
        <stop offset="0" stop-color="var(--sky-gold)"/>
        <stop offset="0.3" stop-color="var(--sky-amber)"/>
        <stop offset="0.5" stop-color="var(--hull-warm)"/>
        <stop offset="0.72" stop-color="var(--sea-mid)"/>
        <stop offset="1" stop-color="var(--sea-deep)"/>
      </linearGradient>
      <radialGradient id="sunGlow" cx="0.96" cy="0.44" r="0.45">
        <stop offset="0" stop-color="var(--sun-core)" stop-opacity="1"/>
        <stop offset="0.3" stop-color="var(--sun-glow)" stop-opacity="0.85"/>
        <stop offset="1" stop-color="var(--sun-glow)" stop-opacity="0"/>
      </radialGradient>
      <radialGradient id="seaGlint" cx="0.9" cy="0.85" r="0.4">
        <stop offset="0" stop-color="var(--glint)" stop-opacity="0.6"/>
        <stop offset="1" stop-color="var(--glint)" stop-opacity="0"/>
      </radialGradient>
    </defs>
    <g fill="none" stroke="var(--rule)" stroke-width="1">
      <polyline points="553,57 1046,57"/>
      <polyline points="979,91 685,91 685,390 751,390"/>
      <polyline points="960,124 720,124 720,216 751,216"/>
    </g>
    <g fill="var(--rule)">
      <circle cx="553" cy="57" r="4.5"/>
      <circle cx="751" cy="216" r="4.5"/>
      <circle cx="751" cy="390" r="4.5"/>
    </g>
  </svg>
  <span class="format-label label-print">PRINT AD</span>
  <span class="format-label label-social">SOCIAL MEDIA AD</span>
  <span class="format-label label-banner">DIGITAL BANNER AD</span>

  <!-- Print ad -->
  <article class="ad ad-print">
    <svg class="photo" viewBox="0 0 500 703" preserveAspectRatio="none" role="img" aria-label="Photograph of a large cruise ship sailing at sunset over a glowing golden sea">
      <clipPath id="clipPrint"><polygon points="500,80 500,703 0,703 0,360"/></clipPath>
      <g clip-path="url(#clipPrint)">
        <rect x="0" y="80" width="500" height="623" fill="url(#sceneTones)"/>
        <rect x="0" y="80" width="500" height="623" fill="url(#sunGlow)"/>
        <rect x="0" y="80" width="500" height="623" fill="url(#seaGlint)"/>
      </g>
    </svg>
    <h1 class="headline">
      <span class="lead">For those<br>who’ve explored<br>the world</span>
      <span class="kicker">and crave something beyond<br>the ordinary.</span>
    </h1>
    <div class="body-copy">
      <p>Each journey is a masterfully curated experience,<br>rich in detail, seamless in execution,<br>and unforgettable in every way.</p>
      <p>We offer an exceptional range of services<br>designed to ensure every journey is flawlessly<br>executed and truly unforgettable.<br>www.tidewelljourneys-example.com</p>
    </div>
    <span class="brand-name">Tidewell Journeys</span>
  </article>

  <!-- Digital banner ad -->
  <article class="ad ad-banner">
    <svg class="photo" viewBox="0 0 365 138" preserveAspectRatio="none" role="img" aria-label="Photograph of a cruise ship at sunset on a golden sea">
      <clipPath id="clipBanner"><polygon points="305,0 365,0 365,138 67,138"/></clipPath>
      <g clip-path="url(#clipBanner)">
        <rect x="0" y="0" width="365" height="138" fill="url(#sceneTones)"/>
        <rect x="0" y="0" width="365" height="138" fill="url(#sunGlow)"/>
        <rect x="0" y="0" width="365" height="138" fill="url(#seaGlint)"/>
      </g>
    </svg>
    <h2 class="headline">
      <span class="lead">For those<br>who’ve<br>explored<br>the world</span>
      <span class="kicker">and crave<br>something<br>beyond the<br>ordinary.</span>
    </h2>
    <span class="brand-name">Tidewell Journeys</span>
  </article>

  <!-- Social media ad -->
  <article class="ad ad-social">
    <svg class="photo" viewBox="0 0 365 365" preserveAspectRatio="none" role="img" aria-label="Photograph of a large cruise ship sailing at sunset over a glowing golden sea">
      <clipPath id="clipSocial"><polygon points="365,58 365,365 0,365 0,267"/></clipPath>
      <g clip-path="url(#clipSocial)">
        <rect x="0" y="58" width="365" height="307" fill="url(#sceneTones)"/>
        <rect x="0" y="58" width="365" height="307" fill="url(#sunGlow)"/>
        <rect x="0" y="58" width="365" height="307" fill="url(#seaGlint)"/>
      </g>
    </svg>
    <h2 class="headline">
      <span class="lead">For those<br>who’ve explored<br>the world</span>
      <span class="kicker">and crave something beyond<br>the ordinary.</span>
    </h2>
    <span class="brand-name">Tidewell Journeys</span>
  </article>

</div>
</body>
</html>
```